Quorva - corporate Business Card

We need a good look and innovative business card for a new start up company based in Los Angeles called "Quorva". We are in a payment business, including payment card, app, and ewallet. We are expert in online payment and Card not present (CNP) transaction.
We need an innovative, modern business card.

Our logo font is Aero Matics

Target Market(s)

Startup - Bank - Online Payment - Card Manufacturing

Industry/Entity Type

Startup

Contact Information for Business Card

phone: 555 014 7396 - Address: 4172 Marlowe blvd, Brenmoor, CA 90299

Requirements
Must have
• Message: innovative, professional, expert, high tech, trust, online payment expert, security
Nice to have
• no comment
Should not have
• no Comment

```html
<!DOCTYPE html>
<html lang="en">
<head>
<meta charset="utf-8">
<title>Quorva Business Card</title>
<link rel="stylesheet" href="https://fonts.googleapis.com/css2?family=Source+Sans+3:wght@400;600&display=swap">
<style>
  :root {
    --brand-red: #b81f2e;
    --card-white: #ffffff;
    --ink: #4a4a4a;
    --rule: #555555;
    --backdrop: #e9e6e2;
  }
  * { margin: 0; padding: 0; box-sizing: border-box; }
  html, body {
    width: 1200px; height: 987px; overflow: hidden;
    background: var(--backdrop);
    font-family: "Source Sans 3", "Myriad Pro", sans-serif;
  }
  .canvas { position: relative; width: 1200px; height: 987px; }
  .card {
    position: absolute; left: 293px; width: 615px; height: 351px;
    box-shadow: 0 2px 6px rgba(0,0,0,0.18);
  }
  .card--front { top: 130px; background: var(--card-white); }
  .card--back { top: 506px; background: var(--brand-red); }

  .brand-mark {
    position: absolute; left: 152px; top: 67px;
    display: flex; align-items: center; gap: 14px;
  }
  .brand-mark__dot {
    width: 94px; height: 94px; border-radius: 50%; background: var(--brand-red);
  }
  .brand-mark__name {
    font-size: 64px; font-weight: 600; color: var(--brand-red); line-height: 1;
    letter-spacing: 1px;
  }

  .contact-rule {
    position: absolute; left: 39px; top: 246px; width: 539px; height: 1px;
    background: var(--rule);
  }
  .contact-row {
    position: absolute; left: 39px; top: 264px; width: 539px; height: 42px;
    font-size: 16.5px; color: var(--ink); line-height: 24px;
  }
  .person { position: absolute; left: 0; top: -4px; }
  .person__name {
    font-size: 21px; font-weight: 600; color: var(--brand-red); line-height: 26px;
  }
  .person__role { font-size: 17px; line-height: 22px; }
  .divider {
    position: absolute; top: 0; width: 1px; height: 42px; background: var(--rule);
  }
  .divider--one { left: 154px; }
  .divider--two { left: 365px; }
  .address { position: absolute; left: 174px; top: -3px; }
  .reach { position: absolute; left: 384px; top: -3px; }
  .reach__line { display: flex; align-items: center; gap: 8px; }
  .reach__icon { width: 15px; height: 15px; fill: var(--brand-red); flex: none; }

  .back-disc {
    position: absolute; left: 213px; top: 72px; width: 188px; height: 188px;
    border-radius: 50%; background: var(--card-white);
    display: flex; align-items: center; justify-content: center;
  }
  .back-disc__name {
    font-size: 44px; font-weight: 600; color: var(--brand-red); letter-spacing: 1px;
  }
  .web-address {
    position: absolute; left: 0; width: 100%; top: 290px; text-align: center;
    color: var(--card-white); font-size: 15px; letter-spacing: 5px;
  }
</style>
</head>
<body>
<main class="canvas">
  <section class="card card--front">
    <div class="brand-mark">
      <div class="brand-mark__dot"></div>
      <span class="brand-mark__name">Quorva</span>
    </div>
    <div class="contact-rule"></div>
    <div class="contact-row">
      <div class="person">
        <div class="person__name">DANA REYES</div>
        <div class="person__role">CEO&amp;Founder</div>
      </div>
      <div class="divider divider--one"></div>
      <div class="address">
        <div>4172 Marlowe blvd</div>
        <div>Brenmoor, CA 90299</div>
      </div>
      <div class="divider divider--two"></div>
      <div class="reach">
        <div class="reach__line">
          <svg class="reach__icon" viewBox="0 0 24 24" aria-hidden="true"><path d="M6.6 10.8a15 15 0 0 0 6.6 6.6l2.2-2.2c.3-.3.7-.4 1-.2 1.1.4 2.3.6 3.6.6.6 0 1 .4 1 1V20c0 .6-.4 1-1 1A17 17 0 0 1 3 4c0-.6.4-1 1-1h3.5c.6 0 1 .4 1 1 0 1.3.2 2.5.6 3.6.1.3 0 .7-.2 1z"/></svg>
          <span>555 014 7396</span>
        </div>
        <div class="reach__line">
          <svg class="reach__icon" viewBox="0 0 24 24" aria-hidden="true"><path d="M2 5h20v14H2z M3.5 6.5 12 13l8.5-6.5" fill="var(--brand-red)" stroke="#fff" stroke-width="1.4"/></svg>
          <span>dana@quorva.com</span>
        </div>
      </div>
    </div>
  </section>

  <section class="card card--back">
    <div class="back-disc"><span class="back-disc__name">Quorva</span></div>
    <div class="web-address">www.quorva.com</div>
  </section>
</main>
</body>
</html>
```